Awesome business card design needed

We need a new business card design to go with our new logo.
We are a web development agency that specialises in highly complex back-end integrations as opposed to design, our customers are retailers, hotels, hospitals and any other organisation that has a large online marketing department.
Take a look at our website - www.brenoloft.com for some inspiration.
We want our new business cards to exude class, professionalism and style.
We are likely to choose a high-end card to print them on but we want the design of the card itself to really turn heads.
We have no specific colour requirements, the logo as you will see is a turquoise colour R89 G171 B167 #59aba7 but it can also be in white if you want to make the colour of the card something different.
The information on the card should be:
Name
Position
Tel
email
Potentially a double sided card could have our web address, twitter and FB links.

```html
<!DOCTYPE html>
<html lang="en">
<head>
<meta charset="utf-8">
<title>Brenoloft Business Card</title>
<link href="https://fonts.googleapis.com/css2?family=Saira:wght@400;600;700&display=swap" rel="stylesheet">
<style>
  :root {
    --turquoise: #59aba7;
    --charcoal: #333435;
    --ink: #2b2b2b;
    --grey: #6b6b6b;
    --paper: #ffffff;
    --backdrop: #e9e9e7;
  }
  * { box-sizing: border-box; margin: 0; padding: 0; }
  html, body { width: 1200px; height: 720px; overflow: hidden; }
  body {
    background: var(--backdrop);
    font-family: "Saira", "Arial", sans-serif;
    position: relative;
  }
  .card {
    position: absolute;
    top: 211px;
    width: 520px;
    height: 297px;
    overflow: hidden;
    box-shadow: 0 6px 18px rgba(0,0,0,0.18);
  }
  .card--front { left: 60px; background: var(--paper); }
  .card--back { left: 620px; background: var(--charcoal); }

  .brand-name {
    position: absolute;
    font-weight: 700;
    color: var(--turquoise);
    letter-spacing: 1px;
    line-height: 1;
  }
  .card--front .brand-name { top: 26px; left: 0; width: 100%; text-align: center; font-size: 62px; }
  .card--back .brand-name { top: 82px; left: 0; width: 100%; text-align: center; font-size: 70px; }

  .identity {
    position: absolute;
    top: 122px;
    right: 266px;
    text-align: right;
  }
  .identity__name { font-size: 17px; font-weight: 700; color: var(--ink); line-height: 1.1; }
  .identity__role { font-size: 12px; color: var(--turquoise); line-height: 1.3; margin-bottom: 3px; }
  .identity__address { font-size: 12px; color: var(--grey); line-height: 1.25; }

  .divider {
    position: absolute;
    top: 120px;
    left: 266px;
    width: 1px;
    height: 76px;
    background: #c9c9c9;
  }
  .contact {
    position: absolute;
    top: 122px;
    left: 280px;
    list-style: none;
  }
  .contact__item {
    display: flex;
    align-items: center;
    gap: 6px;
    font-size: 12.5px;
    color: var(--grey);
    line-height: 1;
    margin-bottom: 9px;
  }
  .contact__icon { width: 12px; height: 12px; flex: none; }

  .wave { position: absolute; left: 0; bottom: 0; width: 520px; height: 297px; }

  .follow {
    position: absolute;
    top: 186px;
    left: 0;
    width: 100%;
    display: flex;
    justify-content: center;
    align-items: center;
    gap: 8px;
  }
  .follow__label { font-size: 18px; font-weight: 700; color: var(--turquoise); margin-right: 4px; }
  .follow__badge { width: 26px; height: 26px; border-radius: 4px; }
  .follow__badge--first { background: #4fb5dd; }
  .follow__badge--second { background: #3f5c9a; }

  .website {
    position: absolute;
    top: 224px;
    left: 0;
    width: 100%;
    text-align: center;
    font-size: 16px;
    color: var(--paper);
    letter-spacing: 1.5px;
  }
  .website strong { font-weight: 700; }
</style>
</head>
<body>
  <section class="card card--front">
    <svg class="wave" viewBox="0 0 520 297" aria-hidden="true">
      <path d="M0 262 C110 300 250 250 360 205 C430 177 480 168 520 172 L520 196 C470 194 420 210 360 236 C250 282 110 306 0 290 Z" fill="var(--turquoise)"/>
      <path d="M0 246 C110 292 250 238 360 196 C430 170 480 162 520 166 L520 172 C480 168 430 177 360 205 C250 250 110 300 0 262 Z" fill="var(--charcoal)"/>
    </svg>

    <div class="brand-name">brenoloft</div>

    <div class="identity">
      <p class="identity__name">Your Name</p>
      <p class="identity__role">Position</p>
      <p class="identity__address">Street Name, City Name<br>State Zip Code</p>
    </div>

    <div class="divider"></div>

    <ul class="contact">
      <li class="contact__item">
        <svg class="contact__icon" viewBox="0 0 12 12" aria-hidden="true">
          <circle cx="6" cy="6" r="5.4" fill="none" stroke="var(--grey)" stroke-width="1"/>
          <path d="M4 3.2 L5 3 L5.6 4.6 L5 5.2 C5.3 6 6 6.7 6.8 7 L7.4 6.4 L9 7 L8.8 8 C6.5 8.4 3.6 5.5 4 3.2 Z" fill="var(--grey)"/>
        </svg>
        123-456-7890
      </li>
      <li class="contact__item">
        <svg class="contact__icon" viewBox="0 0 12 12" aria-hidden="true">
          <circle cx="6" cy="6" r="6" fill="var(--grey)"/>
          <rect x="2.8" y="4" width="6.4" height="4.2" fill="#fff"/>
          <path d="M2.8 4 L6 6.4 L9.2 4" fill="none" stroke="var(--grey)" stroke-width="0.8"/>
        </svg>
        info@brenoloft.com
      </li>
      <li class="contact__item">
        <svg class="contact__icon" viewBox="0 0 12 12" aria-hidden="true">
          <circle cx="6" cy="6" r="6" fill="var(--grey)"/>
          <circle cx="6" cy="6" r="3.6" fill="none" stroke="#fff" stroke-width="0.8"/>
          <ellipse cx="6" cy="6" rx="1.5" ry="3.6" fill="none" stroke="#fff" stroke-width="0.8"/>
          <line x1="2.4" y1="6" x2="9.6" y2="6" stroke="#fff" stroke-width="0.8"/>
        </svg>
        www.brenoloft.com
      </li>
    </ul>
  </section>

  <section class="card card--back">
    <div class="brand-name">brenoloft</div>
    <div class="follow">
      <span class="follow__label">Follow Us On:</span>
      <span class="follow__badge follow__badge--first"></span>
      <span class="follow__badge follow__badge--second"></span>
    </div>
    <p class="website">www.<strong>brenoloft</strong>.com</p>
  </section>
</body>
</html>
```